Harbor Crestline (Business Card Design)

Need business cards designed. Something modern, chic, and sleek. Mabye the back of the card should be the navy blue that is in the logo and then just the logo on the back.

Target Market(s)

Those in the hotel, office, and renovation industry

Contact Information for Business Card

1. Logo 2. Dorian Fenwick 3. CEO/Founder 4. Phone: (833) HarbCre / (833) 427-2731 5. Email: dorian@theharborcrestline.com 6. Website: www.theharborcrestline.com

Font styles to use
Other font styles liked:
• Look at the logo font and base the font for everything else off of that.

Colors
0054AA
0677BA
7BADD7
CADEEF
E8F1F8

Requirements
Must have
• Colors that are associated in the logo
Nice to have
• Sleek modern clean and chic design.

```html
<!DOCTYPE html>
<html lang="en">
<head>
<meta charset="UTF-8">
<title>Harbor Crestline — Business Card</title>
<link rel="stylesheet" href="https://fonts.googleapis.com/css2?family=Montserrat:wght@600&family=Poppins:wght@400;600&display=swap">
<style>
  :root {
    --navy: #111a3e;
    --gold: #c9a03f;
    --ink: #4f4f55;
    --steel: #5b82a8;
    --steel-fade: rgba(91,130,168,0);
    --mist: #dedde3;
    --mist-fade: rgba(222,221,227,0);
    --paper: #ffffff;
    --backdrop: #8c8c8c;
  }
  * { box-sizing: border-box; margin: 0; padding: 0; }
  html, body {
    width: 1200px; height: 959px; overflow: hidden;
    background: var(--backdrop);
  }
  .card {
    position: absolute; left: 295px;
    width: 612px; height: 351px;
    overflow: hidden;
    box-shadow: 0 4px 14px rgba(0,0,0,.35);
  }
  .card-front { top: 103px; background: var(--paper); }
  .card-back  { top: 499px; background: var(--navy); }

  /* front */
  .front-pattern {
    position: absolute; inset: 0;
    background: linear-gradient(210deg, var(--mist) 0%, var(--mist) 30%, var(--mist-fade) 60%);
    clip-path: polygon(401px 59px, 460px 0, 612px 0, 612px 150px, 518px 178px);
  }
  .brand {
    position: absolute; left: 47px; top: 50px;
    display: flex; align-items: center; gap: 30px;
  }
  .brand-square { width: 66px; height: 66px; background: var(--navy); flex: none; }
  .brand-name {
    font-family: "Montserrat", sans-serif; font-weight: 600;
    color: var(--navy); text-transform: uppercase; line-height: 1;
  }
  .brand-name .line-main { display: block; font-size: 34px; letter-spacing: 2px; }
  .brand-name .line-sub  { display: block; font-size: 11px; letter-spacing: 8.4px; margin-top: 7px; padding-left: 3px; }

  .person { position: absolute; left: 143px; top: 178px; right: 29px; }
  .person-name {
    font-family: "Poppins", sans-serif; font-weight: 600;
    font-size: 23px; color: var(--navy); line-height: 1.2;
  }
  .person-role {
    display: flex; align-items: center; gap: 4px;
    font-family: "Poppins", sans-serif; font-weight: 400;
    font-size: 14px; color: var(--gold); line-height: 1.2;
  }
  .role-rule { flex: 1; height: 1px; background: var(--navy); margin-top: 2px; }
  .contacts { list-style: none; margin-top: 22px; }
  .contacts li {
    display: flex; align-items: center; gap: 5px;
    font-family: "Poppins", sans-serif; font-size: 14.5px;
    color: var(--ink); height: 22px;
  }
  .contacts svg { width: 13px; height: 13px; fill: var(--navy); flex: none; }

  /* back */
  .back-pattern {
    position: absolute; inset: 0;
    background: linear-gradient(135deg, var(--steel) 10%, rgba(91,130,168,.55) 50%, var(--steel-fade) 85%);
    clip-path: polygon(0 206px, 72px 80px, 98px 104px, 193px 80px, 401px 291px, 345px 351px, 0 351px);
  }
  .back-brand {
    position: absolute; left: 390px; width: 200px; top: 194px;
    display: flex; flex-direction: column; align-items: center;
    font-family: "Montserrat", sans-serif; font-weight: 600;
    color: var(--paper); text-transform: uppercase; line-height: 1;
  }
  .back-square { width: 44px; height: 44px; background: var(--paper); margin-bottom: 26px; }
  .back-brand .line-main { font-size: 24px; letter-spacing: 2px; }
  .back-brand .line-sub  { font-size: 9px; letter-spacing: 6.4px; margin-top: 6px; padding-left: 6px; }
</style>
</head>
<body>
  <section class="card card-front">
    <div class="front-pattern" role="img" aria-label="Faint brand pattern decoration"></div>
    <div class="brand">
      <span class="brand-square"></span>
      <span class="brand-name">
        <span class="line-main">Harbor</span>
        <span class="line-sub">Crestline</span>
      </span>
    </div>
    <div class="person">
      <h1 class="person-name">Dorian Fenwick</h1>
      <p class="person-role">CEO/Founder<span class="role-rule"></span></p>
      <ul class="contacts">
        <li>
          <svg viewBox="0 0 24 24"><path d="M6.6 10.8a15.2 15.2 0 0 0 6.6 6.6l2.2-2.2a1 1 0 0 1 1-.25 11.4 11.4 0 0 0 3.6.57 1 1 0 0 1 1 1V20a1 1 0 0 1-1 1A17 17 0 0 1 3 4a1 1 0 0 1 1-1h3.5a1 1 0 0 1 1 1c0 1.25.2 2.45.57 3.57a1 1 0 0 1-.25 1z"/></svg>
          (833) HarbCre / (833) 427-2731
        </li>
        <li>
          <svg viewBox="0 0 24 24"><path d="M2 5h20v14H2z"/><path d="M2 5l10 8 10-8" fill="none" stroke="#fff" stroke-width="1.6"/></svg>
          dorian@theharborcrestline.com
        </li>
        <li>
          <svg viewBox="0 0 24 24"><circle cx="12" cy="12" r="9.5" fill="none" stroke="#111a3e" stroke-width="1.8"/><ellipse cx="12" cy="12" rx="4.2" ry="9.5" fill="none" stroke="#111a3e" stroke-width="1.6"/><path d="M2.5 12h19M4 7h16M4 17h16" stroke="#111a3e" stroke-width="1.4"/></svg>
          www.theharborcrestline.com
        </li>
      </ul>
    </div>
  </section>

  <section class="card card-back">
    <div class="back-pattern" role="img" aria-label="Large brand pattern decoration in steel blue"></div>
    <div class="back-brand">
      <span class="back-square"></span>
      <span class="line-main">Harbor</span>
      <span class="line-sub">Crestline</span>
    </div>
  </section>
</body>
</html>
```